Looking for a cool & simple business-card-design for digital agency

Hi!

We are a web agency that offers Reputation Management, Vextor & Seo Services and software development. We like cool things, we like innovative styles.

We have uploaded our logo.

Project Deadline Extended Reason: Client does not want any designs with the colorful logo. Please send us submissions ONLY with the blac and white logo. What the client would like to see:1) Back of the card: is a silver logo on a black background2) front of the card with all the data, please use white background and black logo thank you Added Friday, May 8, 2015

Industry/Entity Type

Software

```html
<!DOCTYPE html>
<html lang="de">
<head>
<meta charset="utf-8">
<title>Pixelhain AG – Business Card</title>
<link rel="stylesheet" href="https://fonts.googleapis.com/css2?family=Lato:wght@400;700;900&display=swap">
<style>
  :root {
    --stage: #e9e7e3;
    --card-black: #0b0b0b;
    --card-white: #ffffff;
    --ink: #111111;
    --silver: #c9c9c9;
    --silver-soft: #9a9a9a;
    --rule: #1a1a1a;
    --shadow: rgba(0, 0, 0, 0.28);
  }
  * { margin: 0; padding: 0; box-sizing: border-box; }
  html, body {
    width: 1200px;
    height: 900px;
    overflow: hidden;
    background: var(--stage);
    font-family: "Lato", Arial, sans-serif;
  }
  .stage {
    position: relative;
    width: 1200px;
    height: 900px;
  }
  .card {
    position: absolute;
    left: 250px;
    width: 700px;
    height: 400px;
    box-shadow: 0 10px 28px var(--shadow);
  }
  .card--back {
    top: 30px;
    background: var(--card-black);
    display: flex;
    align-items: center;
    justify-content: center;
  }
  .card--front {
    top: 470px;
    background: var(--card-white);
    color: var(--ink);
  }
  .brand {
    display: flex;
    align-items: center;
    gap: 18px;
  }
  .brand__mark {
    width: 44px;
    height: 44px;
    flex: none;
  }
  .brand__text { display: flex; flex-direction: column; }
  .brand__name {
    font-weight: 900;
    font-size: 54px;
    line-height: 1;
    letter-spacing: 1px;
  }
  .brand__tagline {
    font-weight: 400;
    font-size: 22px;
    letter-spacing: 9px;
    margin-top: 6px;
  }
  .card--back .brand__mark { background: var(--silver); }
  .card--back .brand__name { color: var(--silver); }
  .card--back .brand__tagline { color: var(--silver-soft); }

  .card--front .brand {
    position: absolute;
    left: 64px;
    top: 48px;
  }
  .card--front .brand__mark { background: var(--ink); width: 38px; height: 38px; }
  .card--front .brand__name { color: var(--ink); font-size: 46px; }
  .card--front .brand__tagline { color: var(--ink); font-size: 19px; letter-spacing: 8px; }

  .person {
    position: absolute;
    left: 34px;
    top: 158px;
  }
  .person__name { font-weight: 700; font-size: 19px; }
  .person__role { font-size: 16px; margin-top: 2px; }
  .rule {
    position: absolute;
    height: 2px;
    background: var(--rule);
  }
  .rule--name { left: 34px; right: 34px; top: 214px; }
  .rule--contact { left: 400px; right: 34px; top: 350px; }

  .contact {
    position: absolute;
    left: 400px;
    top: 236px;
    list-style: none;
    font-size: 19px;
    line-height: 26px;
  }
  .contact__item { display: flex; align-items: center; gap: 8px; }
  .contact__icon { width: 17px; height: 17px; flex: none; }
</style>
</head>
<body>
<main class="stage">

  <section class="card card--back" aria-label="Card back">
    <div class="brand">
      <span class="brand__mark"></span>
      <div class="brand__text">
        <span class="brand__name">PIXELHAIN AG</span>
        <span class="brand__tagline">DIGITALE STRATEGIEN</span>
      </div>
    </div>
  </section>

  <section class="card card--front" aria-label="Card front">
    <div class="brand">
      <span class="brand__mark"></span>
      <div class="brand__text">
        <span class="brand__name">PIXELHAIN AG</span>
        <span class="brand__tagline">DIGITALE STRATEGIEN</span>
      </div>
    </div>

    <div class="person">
      <p class="person__name">Lena Brandt</p>
      <p class="person__role">Director</p>
    </div>
    <div class="rule rule--name"></div>

    <ul class="contact">
      <li class="contact__item">
        <svg class="contact__icon" viewBox="0 0 24 24"><path fill="#111" d="M3 9c0-4 18-4 18 0v2h-5V9H8v2H3zM6 12h12l2 8H4z"/><circle cx="12" cy="16" r="2" fill="#fff"/></svg>
        040 555 0182
      </li>
      <li class="contact__item">
        <svg class="contact__icon" viewBox="0 0 24 24"><rect x="6" y="2" width="12" height="20" rx="2" fill="none" stroke="#111" stroke-width="2"/><rect x="10" y="18" width="4" height="1.5" fill="#111"/></svg>
        079 5550 134
      </li>
      <li class="contact__item">
        <svg class="contact__icon" viewBox="0 0 24 24"><rect x="2" y="5" width="20" height="14" fill="#111"/><path d="M2 5l10 8 10-8" fill="none" stroke="#fff" stroke-width="1.5"/></svg>
        info@pixelhain.com
      </li>
      <li class="contact__item">
        <svg class="contact__icon" viewBox="0 0 24 24"><g fill="none" stroke="#111" stroke-width="2"><circle cx="12" cy="12" r="9"/><ellipse cx="12" cy="12" rx="4" ry="9"/><path d="M3 12h18M5 7h14M5 17h14"/></g></svg>
        www.pixelhain.com
      </li>
    </ul>
    <div class="rule rule--contact"></div>
  </section>

</main>
</body>
</html>
```